Modern Business Card

Modern professional business card with more than just logo and demographic info. Something memorable.

We are a trendy/modern chiropractic group with an emphasis on neurology, hence the minimalist-type brain logo. We want to convey that modern and technical aspect with professionalism and the elite nature of our practice environment.

```html
<!DOCTYPE html>
<html lang="en">
<head>
<meta charset="utf-8">
<title>Kestrel Chiropractic – Business Card</title>
<link rel="stylesheet" href="https://fonts.googleapis.com/css2?family=Cinzel:wght@400;600&family=Crimson+Text:wght@400;600&display=swap">
<style>
  :root {
    --backdrop: #d6d6d8;
    --card-dark: #1b1b1c;
    --card-light: #ffffff;
    --brand-blue: #3f78c8;
    --ink: #2a2a2a;
    --ink-soft: #4a4a4a;
    --rule: #555555;
    --on-dark: #ffffff;
  }
  * { margin: 0; padding: 0; box-sizing: border-box; }
  html, body {
    width: 1200px; height: 960px; overflow: hidden;
    background: var(--backdrop);
  }
  .sheet {
    position: relative; width: 1200px; height: 960px;
    display: flex; flex-direction: column; align-items: center; justify-content: center; gap: 36px;
  }
  .card {
    position: relative; width: 760px; height: 434px;
    border-radius: 26px; overflow: hidden;
    box-shadow: 0 10px 24px rgba(0,0,0,0.22);
  }
  /* Back side */
  .card-back {
    background: var(--card-dark);
    display: flex; align-items: center; justify-content: center;
  }
  .brand {
    display: flex; align-items: center; gap: 22px;
  }
  .brand-square {
    width: 46px; height: 46px; background: var(--brand-blue); border-radius: 6px;
  }
  .brand-name {
    font-family: 'Cinzel', serif; font-weight: 400;
    color: var(--on-dark); font-size: 40px; letter-spacing: 2px; line-height: 1.05;
  }
  /* Front side */
  .card-front { background: var(--card-light); }
  .holder {
    position: absolute; left: 58px; top: 52px;
    font-family: 'Crimson Text', serif;
  }
  .holder-name {
    font-variant: small-caps; color: var(--brand-blue);
    font-size: 32px; letter-spacing: 1px; line-height: 1;
  }
  .holder-role {
    font-variant: small-caps; color: var(--ink);
    font-size: 21px; font-weight: 600; letter-spacing: 1px; margin-top: 2px;
  }
  .address {
    position: absolute; left: 98px; top: 178px;
    font-family: 'Crimson Text', serif; color: var(--ink-soft);
    font-size: 19px; line-height: 1.2;
  }
  .address span { display: block; }
  .address span + span { padding-left: 18px; }
  .contacts {
    position: absolute; left: 112px; top: 236px; list-style: none;
    font-family: 'Crimson Text', serif; color: var(--ink-soft); font-size: 19px; line-height: 1.15;
  }
  .contacts li { display: flex; align-items: center; gap: 10px; }
  .contacts li:nth-child(2) { padding-left: 8px; }
  .contacts li:nth-child(3) { padding-left: 16px; }
  .contacts li:nth-child(4) { padding-left: 24px; }
  .contacts svg { width: 15px; height: 15px; flex: none; fill: var(--brand-blue); }
  .rule {
    position: absolute; left: 0; right: 0; top: 352px;
    height: 1.5px; background: var(--rule);
  }
  .rule-drop {
    position: absolute; left: 98px; top: 352px; width: 1.5px; bottom: 0;
    background: var(--rule);
  }
  .web-pill {
    position: absolute; right: 44px; top: 334px;
    height: 36px; padding: 0 26px; border-radius: 18px;
    background: var(--brand-blue); color: var(--on-dark);
    font-family: 'Crimson Text', serif; font-size: 19px; line-height: 36px; letter-spacing: 0.3px;
  }
</style>
</head>
<body>
<main class="sheet">
  <section class="card card-back" aria-label="Card back">
    <div class="brand">
      <div class="brand-square"></div>
      <div class="brand-name">KESTREL<br>CHIROPRACTIC</div>
    </div>
  </section>

  <section class="card card-front" aria-label="Card front">
    <div class="holder">
      <div class="holder-name">Daniel Hart</div>
      <div class="holder-role">President</div>
    </div>

    <p class="address">
      <span>412 Juniper Court</span>
      <span>Fairview, Oregon 97024</span>
    </p>

    <ul class="contacts">
      <li>
        <svg viewBox="0 0 16 16" aria-hidden="true"><path d="M3.6 1.2l2.2 2.6c.3.4.3.9 0 1.3L4.8 6.3c.9 2 2.6 3.8 4.8 4.8l1.2-1c.4-.3.9-.3 1.3 0l2.6 2.2c.4.3.4.9.1 1.3l-1.2 1.4c-.5.5-1.2.7-1.9.5C6.7 14 2 9.3.5 4.3.3 3.6.5 2.9 1 2.4l1.3-1.2c.4-.4 1-.3 1.3 0z"/></svg>
        <span>555-210-4471</span>
      </li>
      <li>
        <svg viewBox="0 0 16 16" aria-hidden="true"><path d="M4.5 0h7c.8 0 1.5.7 1.5 1.5v13c0 .8-.7 1.5-1.5 1.5h-7C3.7 16 3 15.3 3 14.5v-13C3 .7 3.7 0 4.5 0zM4.6 2v11h6.8V2zM8 13.6a.8.8 0 100 1.6.8.8 0 000-1.6z"/></svg>
        <span>555-318-6602</span>
      </li>
      <li>
        <svg viewBox="0 0 16 16" aria-hidden="true"><path d="M4 1h6l2 2v3H4zM1.5 7h13c.8 0 1.5.7 1.5 1.5V14H0V8.5C0 7.7.7 7 1.5 7zM4 10v2h8v-2z"/></svg>
        <span>555-427-9135</span>
      </li>
      <li>
        <svg viewBox="0 0 16 16" aria-hidden="true"><path d="M0 3h16v1.2L8 9 0 4.2zM0 5.8l8 4.8 8-4.8V13H0z"/></svg>
        <span>hello@kestrelchiro.com</span>
      </li>
    </ul>

    <div class="rule"></div>
    <div class="rule-drop"></div>
    <div class="web-pill">www.kestrelchiro.com</div>
  </section>
</main>
</body>
</html>
```